BrivoTerna. Lantern of the Steady Harvest. Business card

Professional business card for BrivoTerna (Lantern of the Steady Harvest)
My rationale: Strategy-> Execution-> Results-> Value that lead to the BrivoTerna name: We put the Lantern of the Steady Harvest.
We deliver value to our customers helping them at defining a good strategy (cyan arrow). 90% of well formulated strategies fail due to poor execution so we also consider strategical execution very important (green arrow). Due to the execution we obtain the results (blue arrow). Finally, the results provide feedback to redefine strategy, and the new strategy has to be executed and new results obtained providing new feedback and on and on. It's like a wheel that finally, must create corporate value: value for shareholders, staholders, employees, providers...-

Target Market(s)

CEOs and steering comitees , invewrnent funds

Industry/Entity Type

Business Consultant

Contact Information for Business Card

Teodoro Vinsquel
CEO & Founder
teodoro.vinsquel@brivoterna-example.com
Mobile: +34 655.803.912
www.brivoterna-example.com

Colors

Designer to choose colors to be used in the design.

Requirements
Nice to have
• Nice to hace the words: Strategy, execution, results
• Nice to vave the claim: Lantern of the Steady Harvest
• The three colors should be shown:
• cyan for STRATEGY
• green for EXECUTION
• blue for RESULTS
Should not have
• Complete black background

```html
<!DOCTYPE html>
<html lang="en">
<head>
<meta charset="utf-8">
<title>BrivoTerna – Business Card</title>
<link href="https://fonts.googleapis.com/css2?family=Roboto:wght@400;500;700&display=swap" rel="stylesheet">
<style>
  :root {
    --stage: #b4b4b4;
    --paper: #f7f7f7;
    --navy: #0a2b8c;
    --card-blue: #032c8f;
    --pattern-blue: #1746a6;
    --green: #8cc63f;
    --cyan: #1ba9e2;
    --ink: #3a3a3a;
    --white: #ffffff;
  }
  * { box-sizing: border-box; margin: 0; padding: 0; }
  html, body {
    width: 1200px;
    height: 750px;
    overflow: hidden;
    background: var(--stage);
    font-family: "Roboto", Arial, sans-serif;
  }
  .sheet {
    position: relative;
    width: 1200px;
    height: 750px;
  }
  .card {
    position: absolute;
    top: 232px;
    width: 495px;
    height: 283px;
    overflow: hidden;
  }
  .card--front { left: 87px; background: var(--paper); }
  .card--back { left: 618px; background: var(--card-blue); }

  .holder {
    position: absolute;
    left: 37px;
    top: 30px;
  }
  .holder__name {
    font-size: 19px;
    font-weight: 500;
    color: var(--navy);
    line-height: 1.2;
  }
  .holder__role {
    font-size: 15px;
    font-weight: 400;
    color: var(--green);
    line-height: 1.2;
    margin-top: 3px;
  }
  .brand-name {
    position: absolute;
    right: 33px;
    top: 92px;
    font-size: 28px;
    font-weight: 700;
    color: var(--navy);
    letter-spacing: -0.3px;
  }
  .contacts {
    position: absolute;
    left: 0;
    top: 190px;
    list-style: none;
  }
  .contacts__item {
    display: flex;
    align-items: center;
    height: 21px;
    font-size: 12.5px;
    color: var(--ink);
  }
  .contacts__arrow {
    width: 30px;
    height: 14px;
    margin-right: 7px;
    flex: none;
  }
  .back-pattern {
    position: absolute;
    inset: 0;
    background: linear-gradient(135deg, var(--card-blue), #0a37a0 50%, var(--card-blue));
  }
  .back-brand {
    position: absolute;
    right: 40px;
    top: 204px;
    font-size: 14px;
    font-weight: 700;
    color: var(--white);
  }
</style>
</head>
<body>
<main class="sheet">
  <section class="card card--front" aria-label="Business card front">
    <div class="holder">
      <p class="holder__name">Teodoro Vinsquel</p>
      <p class="holder__role">CEO &amp; Founder</p>
    </div>
    <p class="brand-name">BrivoTerna</p>
    <ul class="contacts">
      <li class="contacts__item">
        <svg class="contacts__arrow" viewBox="0 0 30 14" aria-hidden="true"><polygon points="0,4 18,4 18,0 30,7 18,14 18,10 0,10" fill="var(--navy)"/></svg>
        +34 655.803.912
      </li>
      <li class="contacts__item">
        <svg class="contacts__arrow" viewBox="0 0 30 14" aria-hidden="true"><polygon points="0,4 18,4 18,0 30,7 18,14 18,10 0,10" fill="var(--green)"/></svg>
        teodoro.vinsquel@brivoterna-example.com
      </li>
      <li class="contacts__item">
        <svg class="contacts__arrow" viewBox="0 0 30 14" aria-hidden="true"><polygon points="0,4 18,4 18,0 30,7 18,14 18,10 0,10" fill="var(--cyan)"/></svg>
        www.brivoterna-example.com
      </li>
    </ul>
  </section>

  <section class="card card--back" aria-label="Business card back">
    <div class="back-pattern" role="img" aria-label="Repeating brand symbol pattern in soft blue over the deep blue card"></div>
    <p class="back-brand">BrivoTerna</p>
  </section>
</main>
</body>
</html>
```